LHP Regal Business Card Design 2020

Your Manor Steward is looking for a business card that is clean and straight to the point but still looks high-end and attractive. We are a team comprised of management and field professionals focused on the high-end residential marketplace. We serve homeowners and trade professionals directly based out of the Metrowest/Boston area. We provide client services as well as construction/renovation services.
We are aiming for a black and white feel (white background and black text) and a matte finish with rounded edges.

We want to emphasis our vision of "Properties - Projects - Partners".
Dana Pellham is the president of LHP

Please include the following areas we service: Boston/Cape/Newport
Please make sure to include Dana's mobile (555) 213 4480 & office number (555) 640 1937, email dana@yourmanorsteward.example and website www.yourmanorsteward.example

Colors

Designer to choose only greyscale colors for use in the design.

Requirements
Must have
• Include "Properties - Projects - Partners" in design

Include "After Hours Emergency Support # 1800 555 0142" with icon

```html
<!DOCTYPE html>
<html lang="en">
<head>
<meta charset="utf-8">
<title>LHP Business Card</title>
<link rel="stylesheet" href="https://fonts.googleapis.com/css2?family=Poppins:wght@300;400;600;700&display=swap">
<style>
  :root {
    --bg: #3a3b3e;
    --card: #ffffff;
    --ink: #1b1b1d;
    --ink-soft: #4a4a4d;
    --mark: #2a2a2c;
    --rule: #9a9a9a;
  }
  * { margin: 0; padding: 0; box-sizing: border-box; }
  html, body { width: 1200px; height: 800px; overflow: hidden; }
  body {
    background: var(--bg);
    font-family: "Poppins", sans-serif;
    color: var(--ink);
    display: flex;
    align-items: center;
    justify-content: center;
    gap: 40px;
  }
  .card {
    width: 540px;
    height: 310px;
    background: var(--card);
    border-radius: 18px;
    position: relative;
    overflow: hidden;
  }

  /* Front */
  .card-front {
    display: flex;
    flex-direction: column;
    align-items: center;
    justify-content: center;
  }
  .brand-name {
    font-weight: 700;
    font-size: 96px;
    line-height: 1;
    letter-spacing: -2px;
    color: var(--mark);
  }
  .brand-sub {
    font-weight: 700;
    font-size: 15px;
    letter-spacing: 2px;
    color: var(--mark);
    margin-top: 6px;
  }
  .vision {
    font-weight: 300;
    font-size: 14px;
    letter-spacing: 1.5px;
    color: var(--ink-soft);
    margin-top: 22px;
  }

  /* Back */
  .card-back {
    padding: 26px 36px 20px;
    display: flex;
    flex-direction: column;
  }
  .back-main {
    display: flex;
    align-items: center;
    height: 190px;
  }
  .back-brand {
    width: 210px;
    display: flex;
    flex-direction: column;
    align-items: flex-start;
  }
  .back-brand .brand-name { font-size: 74px; color: var(--ink); }
  .back-brand .brand-sub { font-size: 12px; color: var(--ink); letter-spacing: 1.5px; }
  .divider {
    width: 1px;
    height: 140px;
    background: var(--rule);
    margin: 0 24px 0 10px;
  }
  .contact-name {
    font-weight: 700;
    font-size: 17px;
    letter-spacing: 0.5px;
    text-transform: uppercase;
  }
  .contact-title {
    font-weight: 300;
    font-size: 13px;
    color: var(--ink-soft);
    margin-bottom: 10px;
  }
  .contact-list { list-style: none; }
  .contact-list li {
    display: flex;
    align-items: center;
    gap: 8px;
    font-weight: 300;
    font-size: 12.5px;
    line-height: 1.75;
  }
  .contact-list svg, .emergency svg { width: 12px; height: 12px; flex: none; }
  .service-areas {
    font-weight: 300;
    font-size: 14px;
    letter-spacing: 0.5px;
    color: var(--ink-soft);
    text-align: center;
    margin-top: 14px;
  }
  .emergency {
    display: flex;
    align-items: center;
    justify-content: center;
    gap: 8px;
    font-weight: 400;
    font-size: 12.5px;
    margin-top: 8px;
    color: var(--ink);
  }
  .emergency svg { width: 14px; height: 14px; }
</style>
</head>
<body>

  <section class="card card-front">
    <div class="brand-name">LHP</div>
    <div class="brand-sub">YOUR MANOR STEWARD</div>
    <div class="vision">PROPERTIES - PROJECTS - PARTNERS</div>
  </section>

  <section class="card card-back">
    <div class="back-main">
      <div class="back-brand">
        <div class="brand-name">LHP</div>
        <div class="brand-sub">YOUR MANOR STEWARD</div>
      </div>
      <div class="divider"></div>
      <div class="contact">
        <div class="contact-name">Dana Pellham</div>
        <div class="contact-title">President of LHP</div>
        <ul class="contact-list">
          <li>
            <svg viewBox="0 0 12 12" aria-hidden="true"><rect x="3" y="0.5" width="6" height="11" rx="1" fill="none" stroke="currentColor"/><circle cx="6" cy="9.5" r="0.7" fill="currentColor"/></svg>
            (555) 213 4480
          </li>
          <li>
            <svg viewBox="0 0 12 12" aria-hidden="true"><path d="M2.5 1 L4.5 1 L5.2 3.6 L4 4.6 Q5 7 7.4 8 L8.4 6.8 L11 7.5 L11 9.5 Q10.5 11 9 11 Q1 10 1 2.5 Q1 1 2.5 1 Z" fill="currentColor"/></svg>
            (555) 640 1937
          </li>
          <li>
            <svg viewBox="0 0 12 12" aria-hidden="true"><rect x="0.5" y="2" width="11" height="8" fill="currentColor"/><path d="M0.8 2.3 L6 6.5 L11.2 2.3" fill="none" stroke="#ffffff" stroke-width="1"/></svg>
            dana@yourmanorsteward.example
          </li>
          <li>
            <svg viewBox="0 0 12 12" aria-hidden="true"><circle cx="6" cy="6" r="5.3" fill="none" stroke="currentColor"/><ellipse cx="6" cy="6" rx="2.3" ry="5.3" fill="none" stroke="currentColor"/><path d="M0.7 6 H11.3 M1.5 3.5 H10.5 M1.5 8.5 H10.5" stroke="currentColor" stroke-width="0.8"/></svg>
            www.yourmanorsteward.example
          </li>
        </ul>
      </div>
    </div>
    <div class="service-areas">Boston | Metrowest | South Shore | Cape | Newport</div>
    <div class="emergency">
      <svg viewBox="0 0 14 14" aria-hidden="true"><path d="M7 1 L13 12.5 H1 Z" fill="none" stroke="currentColor" stroke-width="1.2" stroke-linejoin="round"/><path d="M7 5 V8.6" stroke="currentColor" stroke-width="1.3"/><circle cx="7" cy="10.4" r="0.75" fill="currentColor"/></svg>
      After Hours Emergency Support # 1800 555 0142
    </div>
  </section>

</body>
</html>
```